Webdesign für Vertrieb und Verkauf von Vellorix Produkten im Firmenbereich
Zielgruppe
Vertrieb und Verkauf von Vellorix Produkten im Firmenbereich (Vellorix KLT, Quorent Flowdesk)
Aufgabenstellung
Ein Logo gibt es auf der bestehenden Internetseite https://www.kelbrotech.eu/ - Dieses Logo bitte beibehalten.
Ansonsten eine schnörkelloses klares Design welches Firmenkunden anspricht und wo man sich schnell zurecht findet.

```html
<!DOCTYPE html>
<html lang="de">
<head>
<meta charset="utf-8">
<title>Vellorix KLT – Vorteile und News</title>
<link href="https://fonts.googleapis.com/css2?family=Bitter:wght@700&family=Kanit:wght@300;400;500&display=swap" rel="stylesheet">
<style>
:root{
  --page:#f2f2f2;
  --white:#ffffff;
  --petrol:#0e5c78;
  --navy:#08344a;
  --accent:#7fd3ef;
  --ink:#333333;
  --dark:#111111;
  --photo-a:#dcdcdc;
  --photo-b:#9a9a9a;
}
*{margin:0;padding:0;box-sizing:border-box}
html,body{width:1200px;height:973px;overflow:hidden;background:var(--page)}
body{font-family:"Kanit",sans-serif;font-weight:300;color:var(--ink);position:relative}
.page{position:absolute;left:167px;top:0;width:867px;height:807px}
.hero{position:absolute;left:0;top:0;width:867px;height:271px;display:flex}
.hero-photo{width:433px;height:271px;background:linear-gradient(135deg,var(--photo-a) 0%,#c8c8c8 45%,var(--photo-b) 100%)}
.benefits{width:434px;height:271px;background:var(--petrol);position:relative;color:var(--white)}
.benefits h2{position:absolute;left:0;width:430px;top:38px;text-align:center;font-family:"Bitter",serif;font-weight:700;font-size:19px}
.benefits .rule{position:absolute;left:188px;top:72px;width:60px;height:3px;background:var(--white)}
.benefit-list{position:absolute;left:130px;top:95px;list-style:none}
.benefit-list li{position:relative;padding-left:27px;height:20.5px;font-size:11.2px;line-height:16px}
.benefit-list svg{position:absolute;left:0;top:2px}
.btn{position:absolute;left:148px;top:205px;width:146px;height:33px;border-radius:17px;background:var(--white);color:var(--dark);font-weight:400;font-size:13.5px;line-height:33px;text-decoration:none;padding-left:36px}
.btn svg{position:absolute;right:22px;top:11px}
.news{position:absolute;left:0;top:271px;width:867px;height:299px;background:var(--white)}
.news-item{position:absolute;width:340px}
.news-item .label{font-weight:500;font-size:10.5px;color:var(--ink);margin-left:1px}
.news-item h3{font-family:"Bitter",serif;font-weight:700;font-size:18.5px;line-height:22.5px;color:#3a3a3a;margin-top:9px;letter-spacing:-.2px}
.news-item .bar{width:60px;height:3px;background:var(--accent);margin-top:12px}
.news-item p{font-size:10.9px;line-height:14.7px;margin-top:11px;margin-left:1px;color:#2e2e2e}
.more{display:inline-flex;align-items:center;gap:8px;margin-top:5px;margin-left:4px;font-weight:500;font-size:11px;color:var(--dark);text-decoration:none}
.footer{position:absolute;left:0;top:570px;width:867px;height:237px;background:var(--navy);color:var(--white);text-align:center}
.footer h2{position:absolute;left:0;width:860px;top:74px;font-weight:500;font-size:15px;line-height:19px}
.footer .rule{position:absolute;left:398px;top:122px;width:60px;height:3px;background:var(--accent)}
.contact{position:absolute;left:0;width:860px;top:134px;font-size:11px;display:flex;justify-content:center;gap:10px;align-items:center}
.contact span{display:inline-flex;align-items:center;gap:5px}
.legal{position:absolute;left:0;width:860px;top:215px;font-size:8.8px;color:var(--accent);font-weight:400}
.legal a{color:var(--accent);text-decoration:none}
</style>
</head>
<body>
<div class="page">
  <section class="hero">
    <div class="hero-photo" role="img" aria-label="Foto: Hände halten ein Tablet mit einem Geschäfts-Dashboard auf einem Schreibtisch"></div>
    <div class="benefits">
      <h2>Das sind Ihre Vorteile</h2>
      <div class="rule"></div>
      <ul class="benefit-list">
        <li><svg width="15" height="12" viewBox="0 0 15 12"><path d="M1 6.5l4 4L14 1" fill="none" stroke="#fff" stroke-width="1.8"/></svg>Duntioriatias et Duntioriatias</li>
        <li><svg width="15" height="12" viewBox="0 0 15 12"><path d="M1 6.5l4 4L14 1" fill="none" stroke="#fff" stroke-width="1.8"/></svg>Koluptionse volupietora</li>
        <li><svg width="15" height="12" viewBox="0 0 15 12"><path d="M1 6.5l4 4L14 1" fill="none" stroke="#fff" stroke-width="1.8"/></svg>Magnares aller Rexcepresser</li>
        <li><svg width="15" height="12" viewBox="0 0 15 12"><path d="M1 6.5l4 4L14 1" fill="none" stroke="#fff" stroke-width="1.8"/></svg>Volorum id que Slantia</li>
      </ul>
      <a class="btn" href="#">Jetzt testen<svg width="7" height="12" viewBox="0 0 7 12"><path d="M1 1l5 5-5 5" fill="none" stroke="#7fd3ef" stroke-width="1.8"/></svg></a>
    </div>
  </section>

  <section class="news">
    <article class="news-item" style="left:76px;top:62px">
      <div class="label">NEWS</div>
      <h3>Ficipid unt quatemo offic Test voloribus mos dolut velores Maquarines</h3>
      <div class="bar"></div>
      <p>Seit über 25 Jahren unterstützt Vellorix KLT die Anfor-derungen von kleinen und mittelständischen Unternehmen. Kunden aus den unterschiedlichsten Branchen setzen die Software für Enterprise Resource Planning (ERP) Tag für Tag erfolgreich ein, bei-spielsweise nternehmen Kunden aus den unterschiedlichsten</p>
      <a class="more" href="#"><svg width="6" height="10" viewBox="0 0 6 10"><path d="M1 1l4 4-4 4" fill="none" stroke="#7fd3ef" stroke-width="1.6"/></svg>weiterlesen</a>
    </article>
    <article class="news-item" style="left:462px;top:63px">
      <div class="label">NEWS</div>
      <h3>Luptiusam ratiatio intalatur Sumlabo Itatur vernatem novacon Elyren</h3>
      <div class="bar"></div>
      <p>Seit über 25 Jahren unterstützt Vellorix KLT die Anfor-derungen von kleinen und mittelständischen Unternehmen. Kunden aus den unterschiedlichsten Branchen setzen die Software für Enterprise Resource Planning (ERP) Tag für Tag erfolgreich ein, bei-spielsweise nternehmen Kunden aus den unterschiedlichsten</p>
      <a class="more" href="#"><svg width="6" height="10" viewBox="0 0 6 10"><path d="M1 1l4 4-4 4" fill="none" stroke="#7fd3ef" stroke-width="1.6"/></svg>weiterlesen</a>
    </article>
  </section>

  <footer class="footer">
    <h2>Sie haben Fragen oder möchten einen<br>Termin vereinbaren?</h2>
    <div class="rule"></div>
    <div class="contact">
      <span><svg width="13" height="10" viewBox="0 0 13 10"><rect x=".7" y=".7" width="11.6" height="8.6" fill="none" stroke="#fff" stroke-width="1.2"/><path d="M1 1l5.5 4.5L12 1" fill="none" stroke="#fff" stroke-width="1.2"/></svg>info@kelbrotech.eu</span>
      <span><svg width="11" height="11" viewBox="0 0 24 24"><path d="M6.6 10.8a15 15 0 006.6 6.6l2.2-2.2c.3-.3.7-.4 1-.2 1.1.4 2.3.6 3.6.6.6 0 1 .4 1 1V20c0 .6-.4 1-1 1A17 17 0 013 4c0-.6.4-1 1-1h3.5c.6 0 1 .4 1 1 0 1.2.2 2.4.6 3.6.1.3 0 .7-.2 1z" fill="#fff"/></svg>+49 (0) 987 6543-2</span>
    </div>
    <div class="legal"><a href="#">IMPRESSUM</a> | <a href="#">DATENSCHUTZ</a> | <a href="#">KONTAKT</a></div>
  </footer>
</div>
</body>
</html>
```